Corporate Business Card

Very professional, Modern, Not to busy, include phone address email, website
(253) 617-4930, 18761 52nd Avenue S, Kent, WA 98047, martin@plumlinegroup.com, varkoworks.com

Target Market(s)

Manufacturing

Industry/Entity Type

Aero, machining, manufacturing, Off road racing

Contact Information for Business Card

Phone, address email, website

```html
<!DOCTYPE html>
<html lang="en">
<head>
<meta charset="utf-8">
<title>Varko Works – Business Card</title>
<link href="https://fonts.googleapis.com/css2?family=Montserrat:wght@500;600;700&display=swap" rel="stylesheet">
<style>
  :root {
    --backdrop: #3a3a3a;
    --brand-red: #d2232a;
    --brand-navy: #1c3470;
    --card-white: #ffffff;
    --ink: #1b1b1b;
    --silver: #c9c9c9;
  }
  * { margin: 0; padding: 0; box-sizing: border-box; }
  html, body {
    width: 1200px; height: 904px; overflow: hidden;
    background: var(--backdrop);
    font-family: "Montserrat", Arial, sans-serif;
  }
  .canvas { position: relative; width: 1200px; height: 904px; }
  .card {
    position: absolute; width: 700px; height: 400px; overflow: hidden;
    box-shadow: 0 10px 24px rgba(0,0,0,.45);
  }
  .card--front { left: 60px; top: 40px; background: var(--brand-red); }
  .card--back { left: 440px; top: 464px; background: var(--card-white); }

  .brand-name {
    position: absolute; font-weight: 700; letter-spacing: 2px;
    text-transform: uppercase; white-space: nowrap;
  }
  .card--front .brand-name {
    color: var(--silver); font-size: 62px;
    left: 0; right: 0; top: 160px; text-align: center;
  }
  .card--back .brand-name {
    color: var(--brand-navy); font-size: 40px; right: 50px; top: 52px;
  }

  .address {
    position: absolute; left: 60px; top: 132px;
    font-size: 16px; font-weight: 500; line-height: 1.35; color: var(--ink);
    font-style: normal;
  }
  .contact-list {
    position: absolute; left: 80px; top: 210px; list-style: none;
    font-size: 16px; font-weight: 500; color: var(--ink);
  }
  .contact-list li { display: flex; align-items: center; gap: 10px; height: 24px; }
  .contact-list svg { width: 15px; height: 15px; flex: none; }
  .swoosh { position: absolute; inset: 0; width: 700px; height: 400px; }
</style>
</head>
<body>
<main class="canvas">
  <section class="card card--front" aria-label="Card front">
    <div class="brand-name">Varko Works</div>
  </section>

  <section class="card card--back" aria-label="Card back">
    <svg class="swoosh" viewBox="0 0 700 400" aria-hidden="true">
      <path d="M0,345 C200,372 380,330 520,240 C600,188 660,168 700,163 L700,175 C660,180 603,200 525,251 C385,343 200,386 0,358 Z" fill="var(--brand-navy)"/>
      <path d="M0,368 C205,394 390,352 530,262 C608,212 662,192 700,188 L700,400 L0,400 Z" fill="var(--brand-red)"/>
    </svg>

    <div class="brand-name">Varko Works</div>

    <address class="address">
      18761 52nd Avenue S<br>Kent, WA 98047
    </address>

    <ul class="contact-list">
      <li>
        <svg viewBox="0 0 16 16"><path d="M4 1l3 3-2 2c1 2 3 4 5 5l2-2 3 3-2 3C7 15 1 9 1 3z" fill="var(--brand-red)"/></svg>
        (253) 617-4930
      </li>
      <li>
        <svg viewBox="0 0 16 16"><rect x="1" y="3" width="14" height="10" fill="var(--brand-red)"/><path d="M1 3l7 6 7-6" fill="none" stroke="#fff" stroke-width="1.4"/></svg>
        martin@plumlinegroup.com
      </li>
      <li>
        <svg viewBox="0 0 16 16"><circle cx="8" cy="8" r="7" fill="var(--brand-red)"/><path d="M1 8h14M8 1c-3 4-3 10 0 14M8 1c3 4 3 10 0 14" fill="none" stroke="#fff" stroke-width="1"/></svg>
        www.varkoworks.com
      </li>
    </ul>
  </section>
</main>
</body>
</html>
```